Webdesign für Vermietung eines Ferienhauses auf der Insel Usedom
Zielgruppe
Vermietung eines Ferienhauses auf der Insel Usedom
ZG: Urlauber im gehobenem Preissegment, die Luxus schätzen und urlauben wollen
Aufgabenstellung
- IN ADOBE PHOTOSHOP
- Bilder können hier entnommen werden: https://www.feriolo-reisen.example/obj-ansicht-quartier/index.php?interface=48213&obj=30597/index.html
- gern können Sie auch Stock-Bilder verwenden
- Der Buchungskalender /die Verfügbarkeit der freien Zeiträume soll präsent im oberen Bereich der Seite stehen
- Zalvix-Bewertungsbutton
- Es gibt kein Logo - bitte den Namenszug 'SEEVILLA*****BROMHOLDE' nutzen

```html
<!DOCTYPE html>
<html lang="de">
<head>
<meta charset="utf-8">
<title>Seevilla Bromholde – 5 Sterne Ferienhaus</title>
<link href="https://fonts.googleapis.com/css2?family=Libre+Baskerville:wght@400;700&family=Raleway:wght@400;500;600;700&display=swap" rel="stylesheet">
<style>
:root{
  --ink:#111111;
  --dark:#0f0f0f;
  --sand:#f1eee9;
  --white:#ffffff;
  --accent:#567270;
  --olive:#2c2a14;
  --line:#dcdcd8;
}
*{margin:0;padding:0;box-sizing:border-box}
html,body{width:1200px;height:3163px;overflow:hidden}
body{font-family:"Raleway",sans-serif;color:var(--ink);background:var(--white);position:relative}

/* wordmark: plain text, one colour, one weight */
.wordmark{font-family:"Libre Baskerville",serif;font-weight:400;font-size:18px;line-height:22px;letter-spacing:2px;color:var(--white);text-align:center}

/* header */
.site-header{position:absolute;top:0;left:0;width:1200px;height:97px;background:var(--white)}
.brand{position:absolute;left:0;top:0;width:283px;height:97px;background:var(--dark);display:flex;align-items:center;justify-content:center}
.main-nav{position:absolute;left:337px;top:40px;display:flex;gap:33px;font-size:14px;letter-spacing:1.2px;color:#333}
.badge{position:absolute;left:1034px;top:22px;width:110px;height:54px;border:2px solid #cfcfcf;border-radius:4px}

/* hero */
.hero{position:absolute;top:97px;left:0;width:1200px;height:481px;
  background:
   linear-gradient(90deg,rgba(70,80,70,.35) 0%,rgba(0,0,0,0) 25%),
   linear-gradient(180deg,#3f4f35 0%,#62704c 18%,#d9dbd4 35%,#eceae4 48%,#7b8c55 62%,#6f8a3e 74%,#b9bbb6 84%,#8e938f 100%)}
.hero-overlay{position:absolute;left:698px;top:0;width:502px;height:481px;background:rgba(30,30,30,.74)}
.booking{position:absolute;left:807px;top:134px;width:284px;color:var(--white)}
.booking h2{font-size:20px;font-weight:600;letter-spacing:.4px}
.fields{display:grid;grid-template-columns:133px 133px;gap:17px 18px;margin-top:16px}
.field{height:32px;background:var(--white);display:flex}
.field .ico{width:32px;height:32px;background:#e4e8f0;display:flex;align-items:center;justify-content:center}
.btn-check{height:32px;background:var(--accent);color:var(--white);font-size:14px;font-weight:500;letter-spacing:.8px;display:flex;align-items:center;justify-content:center}
.divider{display:flex;align-items:center;gap:10px;margin-top:15px;font-size:10px;letter-spacing:2.5px}
.divider::before,.divider::after{content:"";flex:1;height:1px;background:rgba(255,255,255,.8)}
.review{display:flex;justify-content:space-between;align-items:center;margin-top:16px}
.review p{font-size:13px;line-height:15px;width:160px}
.review-btn{width:106px;height:43px;background:var(--white);color:#444;font-weight:600;font-size:18px;display:flex;align-items:center;justify-content:center}

/* features */
.features{position:absolute;top:578px;left:0;width:1200px;height:124px;background:var(--sand)}
.feature{position:absolute;top:27px;width:200px;margin-left:-100px;text-align:center;font-size:11.5px;line-height:18px;color:#555}
.feature svg{display:block;margin:0 auto 6px}

/* welcome */
.welcome{position:absolute;top:702px;left:0;width:1200px;height:673px;background:linear-gradient(#f6f6f5,#ffffff)}
.eyebrow{font-size:11.5px;font-weight:600;letter-spacing:1.5px;display:flex;align-items:center;gap:14px}
.eyebrow::before{content:"";width:56px;height:1px;background:var(--olive)}
.welcome .text{position:absolute;left:101px;top:256px;width:480px}
.welcome h1{font-family:"Libre Baskerville",serif;font-weight:700;font-size:40px;line-height:46px;margin-top:4px;letter-spacing:-.3px}
.welcome p{font-size:14.5px;line-height:24px;margin-top:12px;color:#333;width:470px}
.btn{display:inline-flex;align-items:center;justify-content:center;background:var(--accent);color:var(--white);font-weight:600;letter-spacing:.5px}
.welcome .btn{width:165px;height:41px;font-size:15px;margin-top:30px}
.photo{position:absolute}

/* gallery */
.gallery{position:absolute;top:1375px;left:0;width:1200px;height:644px;background:var(--sand)}
.gallery .head{position:absolute;left:67px;top:86px}
.gallery h2{font-family:"Libre Baskerville",serif;font-weight:700;font-size:39px;margin-top:4px;letter-spacing:-.3px}
.gallery .link{position:absolute;right:66px;top:86px;font-size:11.5px;font-weight:600;letter-spacing:1.5px}
.grid{position:absolute;left:68px;top:171px;width:1066px;display:grid;grid-template-columns:repeat(4,1fr);gap:13px 7px}
.grid div{height:173px}

/* faq */
.faq{position:absolute;top:2019px;left:0;width:1200px;height:496px;background:var(--white)}
.faq .head{position:absolute;left:193px;top:80px}
.faq h2{font-family:"Libre Baskerville",serif;font-weight:700;font-size:35px;margin-top:4px;letter-spacing:-.3px}
.faq-list{position:absolute;left:193px;top:183px;width:558px}
.q{font-size:11.5px;font-weight:700;letter-spacing:1.5px}
.answer{font-size:13.5px;line-height:22px;color:#333;margin-top:10px;padding-bottom:30px;border-bottom:1px solid var(--line)}
.q2{padding:27px 0 27px;border-bottom:1px solid var(--line)}
.q3{padding-top:27px}
.aside{position:absolute;left:859px;top:180px;width:200px}
.aside h3{font-size:11.5px;letter-spacing:1.5px;font-weight:600;color:#555}
.aside p{font-size:13.5px;line-height:23px;margin-top:9px;color:#333;width:150px}
.aside .btn{width:114px;height:32px;font-size:13.5px;font-weight:500;margin-top:18px}

/* map */
.map{position:absolute;top:2515px;left:0;width:1200px;height:370px;
  background:linear-gradient(100deg,#a3a3a3 0%,#b9b9b9 20%,#a5a5a5 35%,#bdbdbd 55%,#c3c3c3 72%,#a0a0a0 88%,#9a9a9a 100%)}
.map .pin{position:absolute;left:880px;top:160px}

/* footer */
.site-footer{position:absolute;top:2885px;left:0;width:1200px;height:278px;background:var(--dark);color:var(--white)}
.site-footer .wordmark{position:absolute;left:67px;top:68px;text-align:left}
.foot-text{position:absolute;left:67px;top:157px;width:270px;font-size:11px;line-height:22px}
.foot-nav{position:absolute;right:67px;top:93px;display:flex;gap:22px;font-size:12.5px}
.foot-line{position:absolute;left:518px;top:129px;width:615px;height:1px;background:rgba(255,255,255,.8)}
.foot-legal{position:absolute;right:67px;top:160px;display:flex;gap:22px;font-size:11px}
</style>
</head>
<body>

<header class="site-header">
  <div class="brand"><span class="wordmark">SEEVILLA<br>BROMHOLDE</span></div>
  <nav class="main-nav">
    <span>Das 5* Strandhaus</span><span>Verfügbarkeit</span><span>Die Räumlichkeiten</span><span>Lage</span><span>Kontakt</span>
  </nav>
  <div class="badge" role="img" aria-label="Klassifizierungssiegel"></div>
</header>

<section class="hero" role="img" aria-label="Garten des Reetdachhauses mit Whirlpool im Vordergrund">
  <div class="hero-overlay"></div>
  <form class="booking">
    <h2>Verfügbarkeit prüfen</h2>
    <div class="fields">
      <div class="field"><span class="ico"><svg width="12" height="12" viewBox="0 0 12 12" fill="none" stroke="#444"><rect x="1.5" y="2.5" width="9" height="8" rx="1"/><path d="M1.5 5h9M4 1v2M8 1v2"/></svg></span></div>
      <div class="field"><span class="ico"><svg width="12" height="12" viewBox="0 0 12 12" fill="none" stroke="#444"><rect x="1.5" y="2.5" width="9" height="8" rx="1"/><path d="M1.5 5h9M4 1v2M8 1v2"/></svg></span></div>
      <div class="field"><span class="ico"><svg width="12" height="12" viewBox="0 0 12 12" fill="none" stroke="#444"><circle cx="4.5" cy="4" r="2"/><path d="M1 10c0-2 1.5-3 3.5-3S8 8 8 10M8 2.2a2 2 0 010 3.6M9.5 7.3c1 .4 1.5 1.3 1.5 2.7"/></svg></span></div>
      <div class="btn-check">Jetzt Prüfen</div>
    </div>
    <div class="divider">ODER</div>
    <div class="review">
      <p>Sehen Sie, was andere Gäste sagen</p>
      <div class="review-btn">Zalvix</div>
    </div>
  </form>
</section>

<section class="features">
  <div class="feature" style="left:158px"><svg width="28" height="24" viewBox="0 0 28 24" fill="var(--olive)"><path d="M14 1L1 12h4v11h7v-7h4v7h7V12h4z"/></svg>145 qm Wohnfläche<br>700qm Grundstück</div>
  <div class="feature" style="left:321px"><svg width="26" height="26" viewBox="0 0 26 26" fill="var(--olive)"><circle cx="7" cy="4" r="3"/><circle cx="19" cy="4" r="3"/><path d="M3 9h8v8H9v8H5v-8H3zM15 9h8l2 9h-3v7h-6v-7h-3z"/></svg>Platz für bis<br>zu 7 Personen</div>
  <div class="feature" style="left:480px"><svg width="28" height="26" viewBox="0 0 28 26" fill="var(--olive)"><path d="M4 12C6 4 16 1 23 6z"/><path d="M13 8l3 1-3 13h-2z"/><rect x="2" y="22" width="24" height="3"/></svg>Nur 5 Gehminuten<br>zum Strand</div>
  <div class="feature" style="left:657px"><svg width="28" height="26" viewBox="0 0 28 26" fill="var(--olive)"><rect x="1" y="4" width="26" height="4"/><path d="M3 8h22v16h-5v-9a6 6 0 00-12 0v9H3z"/><path d="M14 13c3 3 3 6 0 7-3-1-3-4 0-7z"/></svg>Kamin für<br>gemütliche Abende</div>
  <div class="feature" style="left:850px"><svg width="28" height="26" viewBox="0 0 28 26" fill="none" stroke="var(--olive)" stroke-width="2.5"><path d="M8 20V6a3 3 0 016 0M18 20V6a3 3 0 016 0M8 12h10M2 22c3 0 3-2 6-2s3 2 6 2 3-2 6-2 3 2 6 2"/></svg>Eigene Sauna und<br>ganzjährlicher Whirlpool</div>
  <div class="feature" style="left:1056px"><svg width="28" height="26" viewBox="0 0 28 26" fill="var(--olive)"><circle cx="3" cy="5" r="2.5"/><circle cx="3" cy="13" r="2.5"/><circle cx="3" cy="21" r="2.5"/><rect x="8" y="3.5" width="19" height="3"/><rect x="8" y="11.5" width="19" height="3"/><rect x="8" y="19.5" width="19" height="3"/></svg>Entdecken Sie<br>alle Vorteile -&gt;</div>
</section>

<section class="welcome">
  <div class="text">
    <div class="eyebrow">HERZLICH WILLKOMMEN IN IHREM</div>
    <h1>5 Sterne Strandhaus</h1>
    <p>Dieses exklusive, 2017 erbaute Strandhaus mit ca. 145 m² Wohnfläche und einem Grundstück von ca. 700 m² befindet sich ca. 5 Gehminuten vom Strand entfernt.</p>
    <span class="btn">Mehr Erfahren</span>
  </div>
  <div class="photo" role="img" aria-label="Garten mit Lavendel und türkisfarbener Dekoration" style="left:802px;top:175px;width:270px;height:150px;background:linear-gradient(180deg,#2f3d2c 0%,#5d6b55 35%,#8a86a6 60%,#2a9a94 85%,#3c5a40 100%)"></div>
  <div class="photo" role="img" aria-label="Terrasse mit Liegestühlen und Teppich" style="left:836px;top:323px;width:264px;height:178px;background:linear-gradient(180deg,#dcdcd6 0%,#b7ad98 40%,#8a7a60 60%,#c9cac6 75%,#0f8c8f 88%,#2e3530 100%)"></div>
  <div class="photo" role="img" aria-label="Weißes Reetdachhaus mit Terrasse" style="left:655px;top:246px;width:295px;height:195px;background:linear-gradient(180deg,#3a74b0 0%,#6b9acb 22%,#8a7654 38%,#efefec 55%,#e6e6e2 72%,#6f6a55 86%,#4f5c3a 100%)"></div>
</section>

<section class="gallery">
  <div class="head">
    <div class="eyebrow">ENTDECKEN SIE DAS</div>
    <h2>Seevilla Bromholde</h2>
  </div>
  <div class="link">ZUR GALLERIE</div>
  <div class="grid">
    <div role="img" aria-label="Küche mit Kaffeemaschine" style="background:linear-gradient(180deg,#6a6a68 0%,#a4a29c 40%,#5b5550 60%,#dcdcd8 100%)"></div>
    <div role="img" aria-label="Gedeckter Frühstückstisch" style="background:linear-gradient(180deg,#e2e4de 0%,#b6b8ad 40%,#7b6f62 60%,#f0efea 100%)"></div>
    <div role="img" aria-label="Wohnzimmer mit Sofa" style="background:linear-gradient(180deg,#e6e6e0 0%,#cfcdc5 45%,#4d504e 75%,#c9c9c4 100%)"></div>
    <div role="img" aria-label="Essbereich mit Kamin" style="background:linear-gradient(180deg,#e6e8e2 0%,#c4c5bc 40%,#6a6358 65%,#ecebe6 100%)"></div>
    <div role="img" aria-label="Schlafzimmer mit gestreifter Bettwäsche" style="background:linear-gradient(180deg,#efe6d8 0%,#e3d6c2 45%,#d2c08c 70%,#a49270 100%)"></div>
    <div role="img" aria-label="Schlafzimmer mit Holzbett" style="background:linear-gradient(180deg,#ebe6df 0%,#c2aca0 45%,#6d4a36 65%,#e8e0d5 100%)"></div>
    <div role="img" aria-label="Bunte Glasleuchte" style="background:radial-gradient(circle at 45% 45%,#f4e3a0,#b37c3a 35%,#4a3320 80%)"></div>
    <div role="img" aria-label="Stuhl mit Kissen" style="background:linear-gradient(90deg,#4a4d4a 0%,#7c7f78 45%,#e4e5e2 75%,#b8bab5 100%)"></div>
  </div>
  <svg style="position:absolute;left:560px;top:555px" width="80" height="10" viewBox="0 0 80 10"><circle cx="5" cy="5" r="4" fill="#111"/><circle cx="22" cy="5" r="3.5" fill="none" stroke="#888"/><circle cx="39" cy="5" r="3.5" fill="none" stroke="#888"/><circle cx="56" cy="5" r="3.5" fill="none" stroke="#888"/><circle cx="73" cy="5" r="3.5" fill="none" stroke="#888"/></svg>
</section>

<section class="faq">
  <div class="head">
    <div class="eyebrow">HÄUFIGE FRAGEN</div>
    <h2>Schnell beantwortet</h2>
  </div>
  <div class="faq-list">
    <div class="q">WANN IST CHECK-IN? ⌄</div>
    <p class="answer">Lorem ipsum dolor sit amet, consetetur sadipscing elitr, sed diam nonumy eirmod tempor invidunt ut labore et dolore magna aliquyam erat, sed diam voluptua. At vero eos et accusam et justo duo dolores et ea rebum. Stet clita kasd gubergren.</p>
    <div class="q q2">IST EINE LANGZEIT MIETE MÖGLICH? ›</div>
    <div class="q q3">GIBT ES CORONA AUFLAGEN? ›</div>
  </div>
  <aside class="aside">
    <h3>SIE HABEN EINE FRAGE?</h3>
    <p>Sollten Sie noch offene Fragen haben, so kontaktieren Sie uns einfach.</p>
    <span class="btn">Frage stellen</span>
  </aside>
</section>

<section class="map" role="img" aria-label="Graue Umgebungskarte mit Standortmarkierung nahe der Küste">
  <svg class="pin" width="28" height="46" viewBox="0 0 28 46"><circle cx="14" cy="13" r="12" fill="#111"/><rect x="12.5" y="22" width="3" height="22" rx="1.5" fill="#111"/></svg>
</section>

<footer class="site-footer">
  <span class="wordmark">SEEVILLA<br>BROMHOLDE</span>
  <p class="foot-text">Exklusives schilfrohrgedecktes, 2017 erbautes Strandhaus in der 5-Sterne-Haus-Anlage "MERANT Küstenland" in Bromholde.</p>
  <nav class="foot-nav"><span>Das 5* Strandhaus</span><span>Verfügbarkeit</span><span>Die Räumlichkeiten</span><span>Lage</span><span>Kontakt</span></nav>
  <div class="foot-line"></div>
  <nav class="foot-legal"><span>Impressum</span><span>Datenschutz</span></nav>
</footer>

</body>
</html>
```